Redesign of business card for Cedar Ridge Mechanical

We are looking for a new design for our business cards for Cedar Ridge Mechanical. We are a plumbing & HVAC construction company, operating on the West Coast of Canada and USA. Logo attached.
Industry/Entity Type
Construction - Plumbing & HVAC
Contact Information for Business Card
Name, address, phone numbers, email, website address
Look and feel
Each slider illustrates characteristics of the customer's brand and the style your logo design should communicate.

```html
<!DOCTYPE html>
<html lang="en">
<head>
<meta charset="utf-8">
<title>Cedar Ridge Mechanical – Business Card</title>
<link href="https://fonts.googleapis.com/css2?family=Montserrat:wght@400;500;700&display=swap" rel="stylesheet">
<style>
  :root {
    --backdrop: #262626;
    --card: #151515;
    --ink: #ffffff;
    --ink-soft: #e6e6e6;
    --swoosh-grey: #9a9a9a;
    --rule: #d0d0d0;
  }
  * { margin: 0; padding: 0; box-sizing: border-box; }
  html, body {
    width: 1200px; height: 963px; overflow: hidden;
    background: var(--backdrop);
    font-family: "Montserrat", sans-serif;
  }
  .card {
    position: absolute; left: 100px; top: 196px;
    width: 1000px; height: 571px;
    background: var(--card);
    border-radius: 28px;
    overflow: hidden;
    color: var(--ink);
    box-shadow: 0 20px 50px rgba(0,0,0,.5);
  }
  .swoosh { position: absolute; left: 0; top: 0; width: 1000px; height: 571px; }
  .brand {
    position: absolute; left: 70px; top: 150px; width: 330px;
    display: flex; align-items: center; gap: 18px;
  }
  .brand-mark { width: 34px; height: 34px; background: var(--ink); flex: none; }
  .brand-name {
    font-weight: 700; font-size: 30px; line-height: 1.15;
    letter-spacing: 1px; text-transform: uppercase; color: var(--ink);
  }
  .divider {
    position: absolute; left: 440px; top: 120px;
    width: 1.5px; height: 280px; background: var(--rule);
  }
  .contact { position: absolute; left: 480px; top: 130px; }
  .contact-name { font-weight: 700; font-size: 32px; letter-spacing: 1px; text-transform: uppercase; }
  .contact-role { font-weight: 400; font-size: 22px; color: var(--ink-soft); margin-top: 2px; }
  .contact-address { font-weight: 400; font-size: 26px; line-height: 1.2; margin-top: 22px; }
  .contact-list { list-style: none; margin-top: 14px; font-size: 26px; line-height: 1.3; }
  .contact-list li { display: flex; align-items: center; gap: 10px; }
  .contact-list svg { width: 20px; height: 20px; flex: none; }
</style>
</head>
<body>
  <div class="card">
    <svg class="swoosh" viewBox="0 0 1000 571" aria-hidden="true">
      <path d="M0 330 C 250 290, 520 400, 780 571 L 0 571 Z" fill="var(--swoosh-grey)"/>
      <path d="M0 350 C 260 320, 520 430, 740 571 L 0 571 Z" fill="var(--ink)"/>
    </svg>

    <div class="brand">
      <span class="brand-mark"></span>
      <span class="brand-name">Cedar Ridge<br>Mechanical</span>
    </div>

    <div class="divider"></div>

    <div class="contact">
      <p class="contact-name">Jonathan Smith</p>
      <p class="contact-role">Manager</p>
      <p class="contact-address">Your address, city<br>state, ZIP 0000</p>
      <ul class="contact-list">
        <li>
          <svg viewBox="0 0 24 24"><path fill="#fff" d="M6.6 10.8a15 15 0 0 0 6.6 6.6l2.2-2.2c.3-.3.7-.4 1-.2 1.1.4 2.3.6 3.6.6.6 0 1 .4 1 1V20c0 .6-.4 1-1 1A17 17 0 0 1 3 4c0-.6.4-1 1-1h3.5c.6 0 1 .4 1 1 0 1.3.2 2.5.6 3.6.1.3 0 .7-.2 1z"/></svg>
          123-456-2100
        </li>
        <li>
          <svg viewBox="0 0 24 24"><rect x="2" y="5" width="20" height="14" rx="1.5" fill="#fff"/><path d="M3 6.5l9 6.5 9-6.5" fill="none" stroke="#151515" stroke-width="1.6"/></svg>
          youremail@mailbox.com
        </li>
        <li>
          <svg viewBox="0 0 24 24"><circle cx="12" cy="12" r="10" fill="#fff"/><path d="M2 12h20M12 2c3 3 3 17 0 20M12 2c-3 3-3 17 0 20" fill="none" stroke="#151515" stroke-width="1.4"/></svg>
          www.yourwebsite.com
        </li>
      </ul>
    </div>
  </div>
</body>
</html>
```